Dynamic Business Card for Sports Supplements Company

Hi! I'm looking for an awesome business card to match my existing sports supplement company. I have uploaded my current company logo and screenshot of the front page of my website.

I would like to have something dynamic and interesting and utilize the colors in the website - the reds and purples

The business card should be double sided and focus on a unique eye-catching design on the back and include all the relevant company info.

Most importantly, it should say somewhere: "Sign up on our website for a coupon code."

Target Market(s)

Mostly for women gym goers but it shouldn't be too feminine. It should be in keeping with the website design. It should flow and clearly be connected to it

Industry/Entity Type

Business

Contact Information for Business Card

Lorraine K. Vestal
CEO
LVestal@Quorvanexco.com
www.quorvanexco.com
555.417.3820
P.O. Box 47315
Ashvale, Norland 00000

Sign up on our website for a coupon code

Font styles to use
Serif
Sans Serif
Other font styles liked:
• Novecento font family and "Quorvanex" is in AR Destine font

Requirements
Must have
• One side should be a bold Quorvanex logo design. Even just the symbol itself may be o.k. (see attached file)

```html
<!DOCTYPE html>
<html lang="en">
<head>
<meta charset="utf-8">
<title>Quorvanex Business Card</title>
<link rel="stylesheet" href="https://fonts.googleapis.com/css2?family=Exo+2:wght@700;800&family=Open+Sans:wght@400;600&display=swap">
<style>
  :root {
    --backdrop: #e9e9e9;
    --backdrop-light: #f1f1f1;
    --card: #222222;
    --card-back: #1f1f1f;
    --red: #e31e26;
    --white: #ffffff;
    --text-soft: #e4e4e4;
    --divider: #4a2a2c;
  }
  * { box-sizing: border-box; margin: 0; padding: 0; }
  html, body { width: 1200px; height: 900px; overflow: hidden; }
  body {
    position: relative;
    background: radial-gradient(ellipse at 50% 30%, var(--backdrop-light), var(--backdrop) 70%);
    font-family: "Open Sans", Arial, sans-serif;
  }
  .card {
    position: absolute;
    top: 306px;
    width: 440px;
    height: 271px;
    border-radius: 10px;
    overflow: hidden;
    box-shadow: 0 1px 3px rgba(0,0,0,0.18);
  }
  .card--front { left: 149px; background: var(--card); }
  .card--back { left: 608px; background: var(--card-back); }

  .brand {
    position: absolute;
    display: flex;
    align-items: center;
    gap: 8px;
    font-family: "Exo 2", Arial, sans-serif;
    font-weight: 800;
    color: var(--white);
    letter-spacing: 0.5px;
  }
  .brand__mark { background: var(--red); flex: none; }
  .card--front .brand { left: 26px; top: 150px; font-size: 23px; }
  .card--front .brand__mark { width: 14px; height: 14px; }

  .divider {
    position: absolute;
    left: 216px; top: 82px;
    width: 1px; height: 118px;
    background: var(--divider);
  }
  .contact { position: absolute; left: 240px; top: 64px; color: var(--text-soft); font-size: 12px; }
  .contact__name { color: var(--red); font-size: 16px; font-weight: 600; letter-spacing: 0.2px; line-height: 21px; }
  .contact__role { font-size: 12px; line-height: 15px; margin-bottom: 11px; }
  .contact__list { list-style: none; }
  .contact__list li { display: flex; align-items: center; gap: 6px; line-height: 16px; }
  .contact__list svg { width: 8px; height: 8px; fill: var(--red); flex: none; }
  .contact__address { margin-top: 10px; line-height: 16px; font-style: normal; }

  .coupon {
    position: absolute;
    left: 0; right: 0;
    text-align: center;
    font-family: "Exo 2", Arial, sans-serif;
    font-weight: 700;
    font-size: 13.4px;
    color: var(--white);
    letter-spacing: 0.2px;
  }
  .card--front .coupon { top: 228px; }
  .card--back .coupon { top: 224px; }

  .back-pattern {
    position: absolute; inset: 0;
    background: linear-gradient(180deg, #262626, #1d1d1d);
  }
  .card--back .brand { left: 0; right: 0; top: 108px; justify-content: center; font-size: 40px; gap: 12px; }
  .card--back .brand__mark { width: 24px; height: 24px; }
</style>
</head>
<body>
  <section class="card card--front" aria-label="Business card front">
    <div class="brand"><span class="brand__mark"></span><span>QUORVANEX</span></div>
    <div class="divider"></div>
    <div class="contact">
      <p class="contact__name">LORRAINE K. VESTAL</p>
      <p class="contact__role">CEO</p>
      <ul class="contact__list">
        <li><svg viewBox="0 0 10 10"><path d="M2 0.5 L4 2.5 L3 4 Q4.5 6 6 7 L7.5 6 L9.5 8 L8 9.5 Q4 9 0.5 2 Z"/></svg>555.417.3820</li>
        <li><svg viewBox="0 0 10 10"><rect x="0" y="1.5" width="10" height="7"/><path d="M0 1.5 L5 5.5 L10 1.5" stroke="#222" stroke-width="1" fill="none"/></svg>LVestal@Quorvanexco.com</li>
        <li><svg viewBox="0 0 10 10"><circle cx="5" cy="5" r="5"/></svg>www.quorvanexco.com</li>
      </ul>
      <address class="contact__address">P.O. Box 47315<br>Ashvale, Norland 00000</address>
    </div>
    <p class="coupon">SIGN UP ON OUR WEBSITE FOR A COUPON CODE</p>
  </section>

  <section class="card card--back" aria-label="Business card back">
    <div class="back-pattern" role="img" aria-label="Faint repeating brand pattern in dark grey"></div>
    <div class="brand"><span class="brand__mark"></span><span>QUORVANEX</span></div>
    <p class="coupon">SIGN UP ON OUR WEBSITE FOR A COUPON CODE</p>
  </section>
</body>
</html>
```